Tech business card design

We need an amazing business card design for our new business 'Pexla' a marketing tech startup based in Sydney, Australia. We provide an online marketplace for businesses to search and buy advertising media, connect with service providers and learn more about marketing. We wish to communicate 'cool tech', reliability and professionalism and design based around our logo.

Target Market(s)

Business Owners

Contact Information for Business Card

Name
Position
Email Address
Website
Phone Number

Font styles to use
Other font styles liked:
• Avenir & Avenir Next

Colors

Designer to choose colors to be used in the design.

```html
<!DOCTYPE html>
<html lang="en">
<head>
<meta charset="utf-8">
<title>Pexla business card</title>
<link rel="stylesheet" href="https://fonts.googleapis.com/css2?family=Nunito+Sans:wght@300;400;800;900&display=swap">
<style>
  :root {
    --navy: #141640;
    --white: #ffffff;
    --backdrop: #d9d9dc;
    --ink: #141640;
  }
  * { box-sizing: border-box; margin: 0; padding: 0; }
  html, body { width: 1200px; height: 900px; overflow: hidden; }
  body {
    background: radial-gradient(circle at 50% 40%, #ececee 0%, var(--backdrop) 75%);
    font-family: "Nunito Sans", sans-serif;
    color: var(--ink);
    position: relative;
  }
  .card {
    position: absolute;
    left: 280px;
    width: 640px;
    height: 366px;
    border-radius: 24px;
    box-shadow: 0 10px 28px rgba(0,0,0,0.22);
    overflow: hidden;
  }
  .card--front { top: 52px; background: var(--white); border: 9px solid var(--navy); }
  .card--back { top: 470px; background: var(--navy); color: var(--white); }

  .wordmark {
    position: absolute;
    top: 26px;
    left: 34px;
    font-weight: 900;
    font-size: 112px;
    line-height: 1;
    letter-spacing: -3px;
    display: flex;
    align-items: flex-start;
  }
  .wordmark .tm { font-size: 14px; font-weight: 800; letter-spacing: 0; margin: 40px 0 0 6px; }
  .card--front .wordmark { color: var(--navy); top: 18px; left: 26px; }
  .card--back .wordmark { color: var(--white); }

  .identity {
    position: absolute;
    left: 0; right: 0;
    top: 170px;
    text-align: center;
    padding-left: 120px;
  }
  .identity .name { font-weight: 900; font-size: 23px; line-height: 1.05; }
  .identity .role { font-weight: 300; font-size: 21px; line-height: 1.1; }
  .rule { display: block; width: 26px; height: 1.5px; background: currentColor; margin: 16px auto 0; }

  .contact {
    position: absolute;
    left: 0; right: 0;
    top: 252px;
    padding-left: 120px;
    text-align: center;
    font-weight: 300;
    font-size: 19px;
    line-height: 1.12;
  }
  .contact .icons { display: flex; justify-content: center; gap: 6px; margin-bottom: 4px; }
  .contact svg { width: 14px; height: 14px; fill: var(--navy); }

  .card--back .rule { position: absolute; top: 210px; left: 307px; margin: 0; width: 26px; }
  .card--back .site {
    position: absolute;
    right: 40px;
    bottom: 32px;
    font-weight: 300;
    font-size: 24px;
    letter-spacing: 0.5px;
  }
</style>
</head>
<body>
  <section class="card card--front">
    <div class="wordmark">pexla<span class="tm">TM</span></div>
    <div class="identity">
      <p class="name">Marcus Reid</p>
      <p class="role">Founder, Director</p>
      <span class="rule"></span>
    </div>
    <div class="contact">
      <div class="icons">
        <svg viewBox="0 0 16 16" aria-label="phone"><path d="M3.5 1.5l2.6 2.6-1.5 1.7c.9 2 2.6 3.7 4.6 4.6l1.7-1.5 2.6 2.6-2 2.1C6.6 13 3 9.4 1.4 4.5z"/></svg>
        <svg viewBox="0 0 16 16" aria-label="email"><path d="M1 3.5h14v9H1z M1.8 4.3L8 9l6.2-4.7" stroke="#fff" stroke-width="1.1"/></svg>
        <svg viewBox="0 0 16 16" aria-label="web"><circle cx="8" cy="8" r="6.5" fill="none" stroke="#141640" stroke-width="1.4"/><path d="M1.5 8h13M8 1.5c-3 3.5-3 9.5 0 13M8 1.5c3 3.5 3 9.5 0 13" fill="none" stroke="#141640" stroke-width="1.1"/></svg>
      </div>
      <p>+61 (0)400 555 019</p>
      <p>marcus@pexlamedia.com.au</p>
      <p>www.pexlamedia.com.au</p>
    </div>
  </section>

  <section class="card card--back">
    <div class="wordmark">pexla<span class="tm">TM</span></div>
    <span class="rule"></span>
    <p class="site">www.pexlamedia.com.au</p>
  </section>
</body>
</html>
```